Business Card Design

We are a commercial real estate brokerage in San Francisco, leasing office buildings downtown.
I would like a clean, elegant look. Simple but powerful .

Industry/Entity Type

Business

Contact Information for Business Card

Derek Holloway
lic# 07258143
415.555.0172
derek@velt-commercial.example
velt-commercial.example

```html
<!DOCTYPE html>
<html lang="en">
<head>
<meta charset="utf-8">
<title>Velt Commercial — Business Card</title>
<link rel="stylesheet" href="https://fonts.googleapis.com/css2?family=Mulish:wght@400;600;700&display=swap">
<style>
  :root {
    --page: #e9e9ea;
    --silver-light: #ffffff;
    --silver-mid: #e4e5e7;
    --silver-dark: #c9cacd;
    --slate: #6b7a99;
    --slate-deep: #4d586f;
    --ink: #2e2f33;
    --divider: #3a3b3f;
    --white: #ffffff;
  }
  html, body {
    margin: 0;
    width: 1200px;
    height: 806px;
    overflow: hidden;
    background: var(--page);
    font-family: "Mulish", "Century Gothic", sans-serif;
  }
  .card {
    position: absolute;
    left: 40px;
    top: 72px;
    width: 1120px;
    height: 662px;
    overflow: hidden;
    box-shadow: 0 6px 22px rgba(0,0,0,0.18);
  }
  .card-bg { position: absolute; inset: 0; }
  .brand-mark {
    position: absolute;
    left: 150px;
    top: 112px;
    width: 84px;
    height: 84px;
    background: var(--slate);
  }
  .brand-divider {
    position: absolute;
    left: 460px;
    top: 44px;
    width: 4px;
    height: 226px;
    background: var(--divider);
  }
  .brand-name {
    position: absolute;
    left: 488px;
    top: 48px;
    margin: 0;
    color: var(--slate);
    font-weight: 600;
    line-height: 1;
  }
  .brand-name .word-main { display: block; font-size: 142px; letter-spacing: 2px; }
  .brand-name .word-sub { display: block; font-size: 60px; letter-spacing: 1px; margin-top: 2px; }
  .person {
    position: absolute;
    left: 173px;
    top: 286px;
  }
  .person-name { margin: 0; font-size: 36px; font-weight: 700; color: var(--ink); }
  .person-license { margin: 8px 0 0; font-size: 29px; font-weight: 400; color: var(--ink); }
  .contact {
    position: absolute;
    left: 168px;
    top: 440px;
    margin: 0;
    padding: 0;
    list-style: none;
    color: var(--white);
    font-size: 27px;
    font-weight: 700;
  }
  .contact li { display: flex; align-items: center; height: 46px; margin-bottom: 4px; }
  .contact svg { width: 32px; height: 32px; margin-right: 14px; flex: none; }
</style>
</head>
<body>
  <div class="card">
    <svg class="card-bg" width="1120" height="662" viewBox="0 0 1120 662" aria-hidden="true">
      <defs>
        <linearGradient id="silver" x1="0" y1="0" x2="1" y2="0">
          <stop offset="0" stop-color="#cfd0d3"/>
          <stop offset="0.3" stop-color="#ffffff"/>
          <stop offset="0.75" stop-color="#ffffff"/>
          <stop offset="1" stop-color="#c5c6c9"/>
        </linearGradient>
        <linearGradient id="slateBand" x1="0" y1="0" x2="0" y2="1">
          <stop offset="0" stop-color="#6f7d9b"/>
          <stop offset="1" stop-color="#4d586f"/>
        </linearGradient>
      </defs>
      <rect width="1120" height="662" fill="url(#silver)"/>
      <path d="M0,394 C250,425 560,432 720,382 C790,356 790,284 822,272 C900,300 1000,392 1120,396 L1120,662 L0,662 Z" fill="url(#slateBand)"/>
      <path d="M0,394 C250,425 560,432 720,382 C790,356 790,284 822,272 C900,300 1000,392 1120,396" fill="none" stroke="#ffffff" stroke-width="6"/>
    </svg>

    <div class="brand-mark" aria-hidden="true"></div>
    <div class="brand-divider" aria-hidden="true"></div>
    <h1 class="brand-name"><span class="word-main">VELT</span><span class="word-sub">COMMERCIAL</span></h1>

    <div class="person">
      <p class="person-name">Derek Holloway</p>
      <p class="person-license">Lic Nr. 07258143</p>
    </div>

    <ul class="contact">
      <li>
        <svg viewBox="0 0 32 32" aria-hidden="true"><rect x="8" y="3" width="16" height="26" rx="3" fill="none" stroke="#fff" stroke-width="2.4"/><line x1="13" y1="24" x2="19" y2="24" stroke="#fff" stroke-width="2"/></svg>
        415.555.0172
      </li>
      <li>
        <svg viewBox="0 0 32 32" aria-hidden="true"><rect x="3" y="8" width="26" height="17" fill="none" stroke="#fff" stroke-width="2.4"/><path d="M3,8 L16,18 L29,8" fill="none" stroke="#fff" stroke-width="2.4"/></svg>
        derek@velt-commercial.example
      </li>
      <li>
        <svg viewBox="0 0 32 32" aria-hidden="true"><circle cx="16" cy="16" r="13" fill="none" stroke="#fff" stroke-width="2.2"/><ellipse cx="16" cy="16" rx="6" ry="13" fill="none" stroke="#fff" stroke-width="1.8"/><line x1="3" y1="16" x2="29" y2="16" stroke="#fff" stroke-width="1.8"/><line x1="16" y1="3" x2="16" y2="29" stroke="#fff" stroke-width="1.8"/></svg>
        velt-commercial.example
      </li>
    </ul>
  </div>
</body>
</html>
```